Luxury Business Card Design for High-End Window Treatments

Gilded Slatworks
Custom Plantation Shutters & Architectural Shading Systems

⸻

BACK

Daniel Trevick
Owner

Custom Interior & Exterior Window Treatments

919-555-0148
gildedslatworks.com

I have included a picture that I’m hoping we can use on the back, but I’m also wondering if you can get rid of the ladder? Should we get rid of shutters , shades and blinds underneath Gilded Slatworks?

Target Market(s)

High-end residential homeowners, custom home builders, architects, interior designers, and luxury renovation clients seeking premium plantation shutters and motorized architectural shading systems.

Industry/Entity Type

Custom Window treatments

Contact Information for Business Card

Front Gilded Slatworks Custom Plantation Shutters Motorized Architectural Shading Systems BACK Daniel Trevick Owner 919-555-0148 GildedSlatworks.com Custom Interior & Exterior Window Treatments By Appointment

Requirements
Nice to have
• Not 100% sure on nice to halves or the color but you can definitely check out my website to get a better understanding of what I’m trying to do

```html
<!DOCTYPE html>
<html lang="en">
<head>
<meta charset="utf-8">
<title>Gilded Slatworks – Business Card</title>
<link href="https://fonts.googleapis.com/css2?family=Arvo:wght@400;700&family=Montserrat:wght@400;500&display=swap" rel="stylesheet">
<style>
  :root {
    --backdrop: #2b2b2b;
    --card-black: #050505;
    --photo-dark: #1a1a1a;
    --photo-mid: #2e2e2c;
    --gold: #d9b64e;
    --gold-soft: #c9a84a;
    --ivory: #efeadf;
    --white: #f4f4f4;
  }
  * { box-sizing: border-box; margin: 0; padding: 0; }
  html, body {
    width: 1200px; height: 875px; overflow: hidden;
    background: var(--backdrop);
  }
  .stage {
    width: 1200px; height: 875px;
    display: flex; align-items: center; justify-content: center; gap: 40px;
  }
  .card {
    width: 540px; height: 309px;
    border-radius: 18px;
    position: relative; overflow: hidden;
    box-shadow: 0 14px 36px rgba(0,0,0,.5);
  }
  /* Front */
  .card-front { background: var(--photo-dark); }
  .card-front .photo {
    position: absolute; inset: 0;
    background: linear-gradient(160deg, var(--photo-mid) 0%, var(--photo-dark) 55%, #0f0f0f 100%);
  }
  .front-brand {
    position: absolute; left: 0; right: 0; top: 90px;
    text-align: center;
  }
  .brand-name {
    font-family: "Arvo", serif; font-weight: 400;
    font-size: 46px; line-height: 1.05; color: var(--ivory);
  }
  .tagline {
    margin-top: 14px;
    font-family: "Arvo", serif; font-weight: 700;
    font-size: 22px; color: var(--gold); word-spacing: 16px;
  }
  /* Back */
  .card-back { background: var(--card-black); }
  .back-brand {
    position: absolute; left: 30px; top: 112px; width: 250px; text-align: center;
  }
  .back-brand .brand-name { color: var(--gold); font-size: 32px; }
  .back-brand .tagline { font-size: 14px; margin-top: 10px; word-spacing: 8px; }
  .divider {
    position: absolute; left: 300px; top: 62px; width: 1.5px; height: 190px;
    background: var(--white);
  }
  .contact {
    position: absolute; left: 322px; top: 66px; width: 200px;
    font-family: "Montserrat", sans-serif; color: var(--white);
    font-size: 12.5px; line-height: 1.35;
  }
  .contact .person {
    font-family: "Arvo", serif; font-weight: 700; font-size: 21px;
    color: var(--gold); line-height: 1.1;
  }
  .contact .role { margin-bottom: 8px; }
  .contact .service { margin-bottom: 14px; }
  .contact .line { display: flex; align-items: center; gap: 8px; margin-bottom: 4px; }
  .contact .line svg { width: 12px; height: 12px; flex: none; }
  .contact .note { color: var(--gold-soft); margin-top: 6px; }
</style>
</head>
<body>
<main class="stage">
  <section class="card card-front">
    <div class="photo" role="img" aria-label="Darkened photograph of a house front with windows and shutters"></div>
    <div class="front-brand">
      <div class="brand-name">Gilded<br>Slatworks</div>
      <div class="tagline">Shutters Shades Blinds</div>
    </div>
  </section>

  <section class="card card-back">
    <div class="back-brand">
      <div class="brand-name">Gilded<br>Slatworks</div>
      <div class="tagline">Shutters Shades Blinds</div>
    </div>
    <div class="divider"></div>
    <div class="contact">
      <div class="person">Daniel Trevick</div>
      <div class="role">Owner</div>
      <div class="service">Custom Interior &amp; Exterior<br>Window Treatments</div>
      <div class="line">
        <svg viewBox="0 0 12 12" aria-hidden="true"><path fill="var(--white)" d="M1 4c0-2 1-3 5-3s5 1 5 3l-2 1-1-2H4L3 5zM3 6h6l1 5H2z"/></svg>
        <span>919-555-0148</span>
      </div>
      <div class="line">
        <svg viewBox="0 0 12 12" aria-hidden="true"><circle cx="6" cy="6" r="5" fill="none" stroke="var(--white)" stroke-width="1.2"/><path d="M1 6h10M6 1c-3 3-3 7 0 10M6 1c3 3 3 7 0 10" fill="none" stroke="var(--white)" stroke-width="1"/></svg>
        <span>GildedSlatworks.com</span>
      </div>
      <div class="note">By Appointment</div>
    </div>
  </section>
</main>
</body>
</html>
```